Business card for marketing analytics company

Need a business card for new company. I have a logo already that I want to be built into the card and should use those colours

Company is called steered by tallies
Design must bring steered by tallies to life not be a card that could be for anyone with a logo put on it.

Like the front to be fairly clean and uncluttered bringing the logo out with a suitable design on the back of the card.

The logo represents a compass and business growth so those themes along with numbers, analytics , data are appropriate.
I'm often working with creative industries so also needs to reflect the creative side of analytics rather than be very corporate looking.

Target Market(s)

Ad agency, media agency, consumer goods clients

Industry/Entity Type

Market Research

Contact Information for Business Card

Needs to include name, title, email and phone number

Colors
f78f20
f68d4d
ec1f27

Requirements
Must have
• Must bring steered by tallies to life not be a card that could be for anyone with a logo put on it.
• Logo, Correct colours
• Like a design on the back that relates to company name
• Designs for both sides
Should not have
• Please do not just submit logo and a coloured card.
• It needs to have a design element to it
• No black background
• No clear cards - needs front & back

```html
<!DOCTYPE html>
<html lang="en">
<head>
<meta charset="UTF-8">
<title>Steered by Tallies — Business Card</title>
<link href="https://fonts.googleapis.com/css2?family=Montserrat:wght@500;600;700&display=swap" rel="stylesheet">
<style>
  :root {
    --canvas-bg: #e9e7e4;
    --card-white: #ffffff;
    --brand-orange: #f37a24;
    --brand-red: #ec1f27;
    --ink-slate: #4a5560;
    --text-light: #ffffff;
    --card-shadow: 0 18px 40px rgba(0, 0, 0, 0.18);
  }
  * { box-sizing: border-box; margin: 0; padding: 0; }
  html, body {
    width: 1200px;
    height: 1000px;
    overflow: hidden;
    background: var(--canvas-bg);
    font-family: "Montserrat", Arial, sans-serif;
  }
  .canvas {
    position: relative;
    width: 1200px;
    height: 1000px;
  }
  .card {
    position: absolute;
    left: 300px;
    width: 600px;
    height: 340px;
    border-radius: 22px;
    overflow: hidden;
    box-shadow: var(--card-shadow);
    background: var(--card-white);
  }
  .card--front { top: 100px; }
  .card--back  { top: 540px; }

  .wordmark {
    display: flex;
    align-items: center;
    gap: 16px;
  }
  .wordmark__dot {
    width: 58px;
    height: 58px;
    border-radius: 50%;
    border: 5px solid var(--brand-orange);
  }
  .wordmark__name {
    font-weight: 600;
    color: var(--ink-slate);
    line-height: 1.05;
  }

  .card--front .wordmark {
    position: absolute;
    left: 50%;
    top: 50%;
    transform: translate(-50%, -50%);
  }
  .card--front .wordmark__name { font-size: 32px; }

  .back-art {
    position: absolute;
    inset: 0;
    width: 600px;
    height: 340px;
  }
  .card--back .wordmark {
    position: absolute;
    left: 380px;
    top: 130px;
    gap: 12px;
  }
  .card--back .wordmark__dot { width: 46px; height: 46px; border-width: 4px; }
  .card--back .wordmark__name { font-size: 22px; }

  .contact {
    position: absolute;
    left: 40px;
    top: 72px;
    color: var(--text-light);
  }
  .contact__name {
    font-size: 21px;
    font-weight: 700;
    letter-spacing: 0.5px;
  }
  .contact__title {
    font-size: 13px;
    font-weight: 600;
    letter-spacing: 0.6px;
    margin-top: 4px;
  }
  .contact__list {
    list-style: none;
    margin-top: 24px;
  }
  .contact__item {
    display: flex;
    align-items: center;
    gap: 10px;
    font-size: 13.5px;
    font-weight: 500;
    margin-bottom: 7px;
  }
  .contact__icon {
    width: 20px;
    height: 20px;
    flex: none;
  }
  .contact__address {
    margin-top: 20px;
    font-size: 13.5px;
    font-weight: 500;
    line-height: 1.45;
    font-style: normal;
  }
</style>
</head>
<body>
<main class="canvas">

  <section class="card card--front" aria-label="Card front">
    <div class="wordmark">
      <span class="wordmark__dot" aria-hidden="true"></span>
      <span class="wordmark__name">Steered by<br>Tallies</span>
    </div>
  </section>

  <section class="card card--back" aria-label="Card back">
    <svg class="back-art" viewBox="0 0 600 340" aria-hidden="true">
      <rect width="600" height="340" fill="var(--brand-orange)"/>
      <circle cx="560" cy="150" r="258" fill="var(--card-white)"/>
      <circle cx="566" cy="150" r="254" fill="var(--brand-red)"/>
      <circle cx="580" cy="150" r="242" fill="var(--card-white)"/>
      <circle cx="583" cy="150" r="240" fill="var(--brand-orange)"/>
      <circle cx="598" cy="150" r="230" fill="var(--card-white)"/>
    </svg>

    <div class="contact">
      <h1 class="contact__name">DANA WHITFIELD</h1>
      <p class="contact__title">FOUNDER</p>
      <ul class="contact__list">
        <li class="contact__item">
          <svg class="contact__icon" viewBox="0 0 20 20" aria-hidden="true">
            <circle cx="10" cy="10" r="10" fill="var(--text-light)"/>
            <path d="M7 5.5l1.6 2.4-1 1.1c.6 1.3 1.5 2.2 2.8 2.8l1.1-1 2.4 1.6-.8 1.7c-3.6-.2-6.6-3.2-6.8-6.8z" fill="var(--brand-orange)"/>
          </svg>
          000 000 0000
        </li>
        <li class="contact__item">
          <svg class="contact__icon" viewBox="0 0 20 20" aria-hidden="true">
            <circle cx="10" cy="10" r="10" fill="var(--text-light)"/>
            <rect x="5" y="6.5" width="10" height="7" rx="1" fill="var(--brand-orange)"/>
            <path d="M5.5 7l4.5 3.5L14.5 7" fill="none" stroke="var(--text-light)" stroke-width="1"/>
          </svg>
          info@danawhitfield.com
        </li>
        <li class="contact__item">
          <svg class="contact__icon" viewBox="0 0 20 20" aria-hidden="true">
            <circle cx="10" cy="10" r="10" fill="var(--text-light)"/>
            <circle cx="10" cy="10" r="5" fill="none" stroke="var(--brand-orange)" stroke-width="1.3"/>
            <path d="M5 10h10M10 5c-2.4 3-2.4 7 0 10M10 5c2.4 3 2.4 7 0 10" fill="none" stroke="var(--brand-orange)" stroke-width="1"/>
          </svg>
          websitename.com
        </li>
      </ul>
      <address class="contact__address">412 Harbor Crest Road,<br>Suite 210, Marlow, GA 30111</address>
    </div>

    <div class="wordmark">
      <span class="wordmark__dot" aria-hidden="true"></span>
      <span class="wordmark__name">Steered by<br>Tallies</span>
    </div>
  </section>

</main>
</body>
</html>
```